Equipment Finance Specialist I work with companies who need the funds to buy their equipment

I would like a business card that stands out on the shelves. I want to be able to hand it to someone and say WOW. This card should have my logo.
You can put color into it I am very open on design and color

What my company does is we deal with dealerships that sell equipment such as Dump Trucks garbage trucks tractors trailers. Customers get referred to us and depending on their time in business we will ask for the following items

Companies that have been in business for more than two years we have a credit application program up to 250K . With this program we need the following items Credit application filled out(which is what I would like to be able for the customer to click on my website to get.) as well as three current month bank statements.

Deals over 250k we will need the following items

2 years business tax returns
2 years personal tax returns
Profit & Loss statement
Personal Financial Statement

what we do
100% FINANCING
SEASONAL PAYMENTS
LOAN BALLOON PAYMENTS
TRAC LEASING
LOW-INTEREST REFINANCING RATES
DEBT CONSOLIDATION

We specialize in creative financing solutions and offer a variety of reliable, flexible and expandable lending choices.

Target Market(s)

Trucking Companies

Industry/Entity Type

Trucking Company

Contact Information for Business Card

* $250,000 Application only Program
* Loans from $30,000 to 5,000,000
* Competitive Interest Rates

Font styles to use
Serif
Sans Serif

Colors

Designer to choose colors to be used in the design.

Requirements
Must have
• On the back of the card.
• * $250,000 Application only Program
• * Loans from $30,000 to 5,000,000
• My name, email, website. address
• * Competitive Interest Rates
• * 100% Financing
Nice to have
• I want my logo to pop on the card
• My logo is the great one I would like to use
Should not have
• I am up for your creativity as well

```html
<!DOCTYPE html>
<html lang="en">
<head>
<meta charset="utf-8">
<title>Summit Haul Capital — Business Card</title>
<link rel="stylesheet" href="https://fonts.googleapis.com/css2?family=Play:wght@400;700&family=Open+Sans:wght@400;600&display=swap">
<style>
  :root {
    --navy: #1d3a78;
    --red: #c00d2f;
    --ink: #4b4f57;
    --paper: #ffffff;
    --ghost: #e6e9f0;
    --stage: #2b2b2b;
    --white: #ffffff;
  }
  * { box-sizing: border-box; margin: 0; padding: 0; }
  html, body {
    width: 1125px; height: 1200px; overflow: hidden;
    background: var(--stage);
  }
  .card {
    position: absolute; left: 150px; width: 826px; height: 471px;
    overflow: hidden;
  }
  .card--front { top: 98px; background: var(--paper); }
  .card--back { top: 631px; background: var(--red); }

  /* front */
  .brand {
    position: absolute; left: 46px; top: 95px;
    display: flex; align-items: center; gap: 16px;
    font-family: "Play", sans-serif; font-weight: 700;
    font-size: 44px; color: var(--navy); letter-spacing: 0.5px;
    text-transform: uppercase;
  }
  .brand__dot {
    width: 54px; height: 54px; border-radius: 50%; background: var(--navy);
    flex: none;
  }
  .hero-art {
    position: absolute; left: 380px; top: 55px; width: 446px; height: 416px;
    background: radial-gradient(ellipse at 60% 55%, #e3e7ef 0%, #eef0f5 55%, rgba(255,255,255,0) 80%);
  }
  .address {
    position: absolute; left: 48px; top: 280px;
    font-family: "Play", sans-serif; font-weight: 700; font-size: 19.5px;
    line-height: 26px; color: var(--ink);
  }
  .contacts {
    position: absolute; left: 48px; top: 340px; list-style: none;
    font-family: "Play", sans-serif; font-weight: 700; color: var(--ink);
  }
  .contacts li { display: flex; align-items: center; height: 27px; font-size: 18.5px; }
  .contacts li:first-child { font-size: 21px; height: 30px; }
  .contacts svg { width: 20px; height: 18px; margin-right: 17px; fill: var(--navy); flex: none; }
  .person {
    position: absolute; right: 48px; top: 330px; text-align: right;
    font-family: "Play", sans-serif; font-weight: 700;
  }
  .person__name { font-size: 26px; color: var(--navy); line-height: 30px; }
  .person__title { font-size: 19px; color: var(--red); line-height: 22px; }

  /* back */
  .back-brand {
    position: absolute; left: 0; right: 0; top: 190px;
    display: flex; justify-content: center; align-items: center; gap: 16px;
    font-family: "Play", sans-serif; font-weight: 700; font-size: 40px;
    color: var(--white); text-transform: uppercase;
  }
  .back-brand__ring {
    width: 56px; height: 56px; border-radius: 50%; border: 5px solid var(--white); flex: none;
  }
  .offers {
    position: absolute; left: 0; right: 0; top: 385px; text-align: center;
    font-family: "Open Sans", sans-serif; font-size: 19.5px; line-height: 27px;
    color: var(--white);
  }
</style>
</head>
<body>
  <section class="card card--front">
    <div class="hero-art" role="img" aria-label="Faint large illustration of a dump truck cab"></div>
    <div class="brand"><span class="brand__dot"></span>Summit Haul Capital</div>

    <p class="address">2710 Harborview Lane<br>Millbrook, NY 12545</p>

    <ul class="contacts">
      <li><svg viewBox="0 0 20 18"><path d="M2 6c0-3 3-4 8-4s8 1 8 4v2h-4V6H6v2H2z M4 9h12l2 8H2z"/></svg>555 0142 7781</li>
      <li><svg viewBox="0 0 20 18"><path d="M1 4h18v1l-9 6-9-6z M1 7l9 6 9-6v8H1z"/></svg>mark@summithaulcapital.com</li>
      <li><svg viewBox="0 0 20 18"><circle cx="10" cy="9" r="8"/></svg>www.summithaulcapital.com</li>
    </ul>

    <div class="person">
      <p class="person__name">MARK DELANO</p>
      <p class="person__title">PRESIDENT</p>
    </div>
  </section>

  <section class="card card--back">
    <div class="back-brand"><span class="back-brand__ring"></span>Summit Haul Capital</div>
    <p class="offers">
      $250,000 Application only Program &#9679; Loans from $30,000 to 5,000,000<br>
      Competitive Interest Rates &#9679; 100% Financing
    </p>
  </section>
</body>
</html>
```